Biz Card

MARKETING today is the most rapidly changing business discipline. Media options to reach customers, actual customer preferences and consumer buying decisions change by the minute . . . no, by the second. The behavioral data generated by all aspects of the business and the new technologies that put the data to work together produce the potential to generate business intelligence and guide smart resource allocation to influence purchase and retention. However, to realize this potential, marketing professionals at all levels and in all organizations must continuously improve their skills not just from on-the-job training but by learning from masters in the field. The Bright Horizon Guild is the training center that serves this professional development need.model logos:msi.orgama.orgcontentmarketinginstitute.comBook covers on MarketingMetrics, Marketing Anaytics
Industry/Entity Type
Business
Contact Information for Business Card
Roy A. YoungCEOMarketing Science Academyphone: 310-601-4755email: roy@marketingscience.comAddress:437 South Rexford DriveBeverly Hills, CA 89377
Look and feel
Each slider illustrates characteristics of the customer's brand and the style your logo design should communicate.

```html
<!DOCTYPE html>
<html lang="en">
<head>
<meta charset="utf-8">
<title>Bright Horizon Guild – Business Card</title>
<link rel="stylesheet" href="https://fonts.googleapis.com/css2?family=Roboto:wght@400;500;700&display=swap">
<style>
  :root {
    --page-bg: #e9e7e5;
    --card-black: #161616;
    --card-black-mark: #2c2c2c;
    --card-white: #ffffff;
    --brand-red: #8e1c1c;
    --stripe-grey: #4a4a4a;
    --text-dark: #3c3c3c;
    --text-muted: #6a6a6a;
  }
  * { box-sizing: border-box; margin: 0; padding: 0; }
  html, body {
    width: 1200px; height: 716px; overflow: hidden;
    background: var(--page-bg);
    font-family: "Roboto", Arial, sans-serif;
  }
  .stage { position: relative; width: 1200px; height: 716px; }
  .card {
    position: absolute; top: 215px;
    width: 500px; height: 286px;
    box-shadow: 0 6px 18px rgba(0,0,0,0.18);
  }
  /* Front */
  .card-front {
    left: 70px; background: var(--card-black);
    display: flex; align-items: center; justify-content: center;
  }
  .front-name {
    color: var(--card-black-mark);
    font-weight: 700; font-size: 30px; letter-spacing: 0.5px;
    text-transform: uppercase;
  }
  /* Back */
  .card-back { left: 630px; background: var(--card-white); overflow: hidden; }
  .edge-red {
    position: absolute; left: 0; top: 0; bottom: 0; width: 30px;
    background: var(--brand-red);
  }
  .edge-grey {
    position: absolute; left: 30px; top: 0; bottom: 0; width: 5px;
    background: var(--stripe-grey);
  }
  .brand-block {
    position: absolute; top: 40px; right: 30px;
    display: flex; align-items: center; gap: 16px;
  }
  .brand-divider { width: 1px; height: 74px; background: var(--text-muted); }
  .brand-name {
    color: var(--text-dark); font-weight: 700; font-size: 19px;
    line-height: 1.02; text-transform: uppercase; letter-spacing: 0.3px;
  }
  .person { position: absolute; left: 62px; top: 118px; }
  .person-name { color: var(--brand-red); font-weight: 700; font-size: 17px; }
  .person-title { color: var(--text-muted); font-size: 10px; margin-top: 4px; }
  .contact-list {
    position: absolute; left: 62px; top: 178px; list-style: none;
  }
  .contact-list li {
    display: flex; align-items: center; gap: 10px;
    color: var(--text-dark); font-size: 12px; line-height: 20px;
  }
  .contact-list svg { width: 11px; height: 11px; fill: var(--brand-red); flex: none; }
</style>
</head>
<body>
<main class="stage">
  <section class="card card-front" aria-label="Card front">
    <span class="front-name">Bright Horizon Guild</span>
  </section>

  <section class="card card-back" aria-label="Card back">
    <div class="edge-red"></div>
    <div class="edge-grey"></div>

    <div class="brand-block">
      <div class="brand-divider"></div>
      <div class="brand-name">Bright<br>Horizon<br>Guild</div>
    </div>

    <div class="person">
      <div class="person-name">Neil P. Barton</div>
      <div class="person-title">CEO</div>
    </div>

    <ul class="contact-list">
      <li>
        <svg viewBox="0 0 12 12" aria-hidden="true"><path d="M2.5 1 L4.5 1 L5.3 3.6 L4 4.6 Q5 6.8 7.4 8 L8.4 6.7 L11 7.5 L11 9.5 Q10.5 11 9 11 Q1 10 1 3 Q1 1.5 2.5 1Z"/></svg>
        310-555-0182
      </li>
      <li>
        <svg viewBox="0 0 12 12" aria-hidden="true"><path d="M1 2.5 H11 V9.5 H1Z M1.6 3 L6 6.5 L10.4 3" fill="none" stroke="#8e1c1c" stroke-width="1.2"/></svg>
        neil@brighthorizonguild.com
      </li>
      <li>
        <svg viewBox="0 0 12 12" aria-hidden="true"><g fill="none" stroke="#8e1c1c" stroke-width="1.1"><circle cx="6" cy="6" r="5"/><ellipse cx="6" cy="6" rx="2.2" ry="5"/><path d="M1 6 H11"/></g></svg>
        www.brighthorizonguild.com
      </li>
      <li>
        <svg viewBox="0 0 12 12" aria-hidden="true"><path d="M6 0.5 A4 4 0 0 1 10 4.5 Q10 7.5 6 11.5 Q2 7.5 2 4.5 A4 4 0 0 1 6 0.5Z M6 3 A1.5 1.5 0 1 0 6 6 A1.5 1.5 0 1 0 6 3Z" fill-rule="evenodd"/></svg>
        912 North Calloway Lane Beverly Hills, CA 89377
      </li>
    </ul>
  </section>
</main>
</body>
</html>
```